Brightwell Supports

We need an updated website that captures the comprehensive services and supports we provide to persons with developmental disabilities. We need a website design that educates families about the services we provide. We would also need a website that is user-friendly so that we could periodically update training schedules and ongoing programming.

• Thank you for submitting designs.  A few things I am hoping to see offered in the website:
• Front page highlights the services we offer (host homes, family caregiver, day program, employment program, SLS program, supported apartment program, behavior/clinical program)
• Front page also highlights any new programs we want to make prominent:  family caregiver, future restaurant employment openings, etc...
• Interactive Training Calendar
• Employee Resources page (link to carevo, email login, etc.)
• Uniform provider application for host home providers
• Information on agency - history, goals, etc.
• Contact Information/Location

 

Fun things to include:

• Client Highlights (featuring a client story each month, etc...)
• Employee highlights (featuring a staff member...)
• link to other Brightwell business pages (Brightwell Therapy and Brightwell Restaurant)

```html
<!DOCTYPE html>
<html lang="en">
<head>
<meta charset="utf-8">
<title>Brightwell Supports</title>
<link href="https://fonts.googleapis.com/css2?family=Open+Sans:wght@400;600&display=swap" rel="stylesheet">
<style>
:root{
  --brand-red:#8e2424;
  --nav-dark:#262626;
  --nav-mid:#3a3a3a;
  --text:#222;
  --muted:#444;
  --panel:#f8f8f8;
  --line:#e6e6e6;
  --footer:#4a4a4a;
}
*{margin:0;padding:0;box-sizing:border-box}
html,body{width:878px;height:1200px;overflow:hidden;background:#fff}
body{position:relative;font-family:"Open Sans",Arial,sans-serif;color:var(--text)}
.abs{position:absolute}

/* header */
.brand{left:126px;top:36px;display:flex;align-items:center;gap:8px}
.brand-dot{width:18px;height:18px;border-radius:50%;background:var(--brand-red)}
.brand-name{font-size:20px;font-weight:600;color:var(--nav-dark)}
.call{left:636px;top:28px;display:flex;gap:10px;align-items:flex-start}
.call-text{font-size:12px;line-height:24px;color:var(--text)}

/* nav */
.nav{left:0;top:94px;width:878px;height:38px;background:linear-gradient(var(--nav-mid),var(--nav-dark));border-top:2px solid var(--brand-red)}
.nav-home{position:absolute;left:126px;top:0;width:59px;height:36px;background:var(--brand-red);display:flex;align-items:center;justify-content:center}
.nav-item{position:absolute;top:0;height:36px;line-height:36px;font-size:9.5px;font-weight:600;color:#fff}
.nav-sep{position:absolute;top:4px;width:1px;height:28px;background:#4c4c4c}

/* hero */
.hero{left:0;top:132px;width:878px;height:354px;background:linear-gradient(135deg,#e9ecef 0%,#d6dbe0 40%,#f2f3f5 70%,#e4e7ea 100%)}
.hero-caption{left:173px;top:290px;width:523px;height:49px;background:rgba(60,60,60,.82);color:#fff;font-size:15.5px;line-height:49px;text-align:center}
.hero-arrow{top:300px;width:28px;height:28px;border-radius:50%;background:rgba(255,255,255,.8);display:flex;align-items:center;justify-content:center}

/* features */
.features{left:0;top:486px;width:878px;height:258px;background:var(--panel);border-top:1px solid var(--line);border-bottom:1px solid var(--line)}
.feature{position:absolute;width:214px;height:100px}
.feature-icon{position:absolute;left:0;top:0;width:68px;height:68px;border-radius:50%;background:#fff;border:1px solid #e8e8e8;box-shadow:0 0 0 3px #f1f1f1 inset;display:flex;align-items:center;justify-content:center}
.feature-title{position:absolute;left:77px;top:-6px;font-size:11.5px;color:var(--text)}
.feature-text{position:absolute;left:77px;top:16px;width:123px;font-size:7.2px;line-height:13.6px;text-align:justify;color:var(--muted)}

/* welcome */
.section-title{font-size:15.5px;font-weight:400;color:var(--text)}
.section-title span{color:var(--brand-red)}
.rule{height:1px;background:var(--line)}
.welcome-photo{left:126px;top:812px;width:285px;height:136px;border:1px solid #ddd;padding:3px;background:#fff}
.welcome-photo div{width:100%;height:100%;background:linear-gradient(180deg,#3e4446 0%,#566a3a 45%,#6b5b55 75%,#8a2a2f 100%)}
.welcome-text{left:126px;top:963px;width:285px;font-size:7.2px;line-height:13.6px;text-align:justify;color:var(--muted)}
.btn{left:126px;top:1072px;width:72px;height:28px;background:#444;border-radius:3px;color:#fff;font-size:8.5px;line-height:28px;text-align:center}

/* posts */
.post{position:absolute;left:453px;width:301px;height:136px;border:1px solid var(--line);background:#fbfbfb}
.post-photo{position:absolute;left:13px;top:12px;width:102px;height:96px;border:1px solid #ddd;padding:2px;background:#fff}
.post-photo div{width:100%;height:100%}
.post-title{position:absolute;left:127px;top:11px;font-size:10.5px;color:var(--text)}
.post-date{position:absolute;left:127px;top:38px;font-size:7px;color:var(--muted)}
.post-text{position:absolute;left:127px;top:58px;width:161px;font-size:7.2px;line-height:13.6px;text-align:justify;color:var(--muted)}
.post-more{position:absolute;right:15px;top:114px;font-size:7.2px;color:var(--brand-red);font-weight:600}

/* footer */
.footer{left:0;top:1133px;width:878px;height:67px;background:var(--footer);border-top:3px solid var(--brand-red)}
.footer-links{position:absolute;left:127px;top:18px;font-size:7.5px;color:#ddd}
.footer-copy{position:absolute;left:125px;top:40px;font-size:7.5px;color:#ddd}
.social{position:absolute;top:29px;width:15px;height:15px;border-radius:50%;background:#f2f2f2}
</style>
</head>
<body>

<header>
  <div class="abs brand"><span class="brand-dot"></span><span class="brand-name">Brightwell Supports</span></div>
  <div class="abs call">
    <svg width="20" height="32" viewBox="0 0 20 32"><rect x="1.5" y="1.5" width="17" height="29" rx="3" fill="none" stroke="#111" stroke-width="2.5"/><rect x="4" y="6" width="12" height="18" fill="#111"/><circle cx="10" cy="27" r="1.3" fill="#111"/></svg>
    <div class="call-text">Call For Info<br>+1-555-014-2290</div>
  </div>
</header>

<nav class="abs nav">
  <div class="nav-home"><svg width="18" height="15" viewBox="0 0 18 15"><path d="M9 0 18 8h-3v7h-4v-5H7v5H3V8H0z" fill="#fff"/></svg></div>
  <span class="nav-item" style="left:208px">Services</span>
  <span class="nav-sep" style="left:259px"></span>
  <span class="nav-item" style="left:275px">Residential Program</span>
  <span class="nav-sep" style="left:379px"></span>
  <span class="nav-item" style="left:395px">SLS Program</span>
  <span class="nav-sep" style="left:462px"></span>
  <span class="nav-item" style="left:478px">Employee Resources</span>
  <span class="nav-sep" style="left:575px"></span>
  <span class="nav-item" style="left:588px">Meet Our Team!</span>
  <span class="nav-sep" style="left:670px"></span>
  <span class="nav-item" style="left:683px">Contact Us</span>
</nav>

<section class="abs hero" role="img" aria-label="Photo of a person working at a desk with a tablet, glasses and paperwork"></section>
<div class="abs hero-arrow" style="left:77px"><svg width="8" height="10"><path d="M6 1 2 5l4 4" fill="none" stroke="#555" stroke-width="1.6"/></svg></div>
<div class="abs hero-arrow" style="left:766px"><svg width="8" height="10"><path d="M2 1l4 4-4 4" fill="none" stroke="#555" stroke-width="1.6"/></svg></div>
<div class="abs hero-caption">Building Abilities ~ Creating Opportunities ~ Developing Relationships</div>

<section class="abs features">
  <div class="feature" style="left:125px;top:44px">
    <div class="feature-icon"><svg width="28" height="28" viewBox="0 0 28 28"><circle cx="13" cy="8" r="6" fill="#111"/><path d="M3 27c0-8 4-12 10-12s8 3 9 6l-4 6z" fill="#111"/><path d="M20 20l5-6 2 2-5 6z" fill="#111"/></svg></div>
    <div class="feature-title">Employment Program</div>
    <div class="feature-text">Brightwell Supports provides intensive and ongoing supports that enable clients that may otherwise</div>
  </div>
  <div class="feature" style="left:339px;top:44px">
    <div class="feature-icon"><svg width="20" height="32" viewBox="0 0 20 32"><rect x="1.5" y="1.5" width="17" height="29" rx="3" fill="none" stroke="#111" stroke-width="2.5"/><rect x="4" y="6" width="12" height="18" fill="#111"/><circle cx="10" cy="27" r="1.3" fill="#111"/></svg></div>
    <div class="feature-title">Community Resources</div>
    <div class="feature-text">Brightwell Supports provides intensive and ongoing supports that enable clients that may otherwise</div>
  </div>
  <div class="feature" style="left:553px;top:44px">
    <div class="feature-icon"><svg width="28" height="28" viewBox="0 0 28 28"><rect x="2" y="5" width="21" height="21" rx="3" fill="none" stroke="#111" stroke-width="2.5"/><path d="M10 18l1-5 11-11 4 4-11 11z" fill="#111"/></svg></div>
    <div class="feature-title">Residential Program</div>
    <div class="feature-text">Brightwell Supports provides intensive and ongoing supports that enable clients that may otherwise</div>
  </div>
  <div class="feature" style="left:125px;top:157px">
    <div class="feature-icon"><svg width="36" height="30" viewBox="0 0 36 30"><circle cx="9" cy="8" r="5" fill="#111"/><circle cx="27" cy="8" r="5" fill="#111"/><circle cx="18" cy="17" r="5" fill="#111"/><path d="M1 22c0-5 3-8 8-8h2v8zM35 22c0-5-3-8-8-8h-2v8zM9 30c0-5 4-8 9-8s9 3 9 8z" fill="#111"/></svg></div>
    <div class="feature-title">Client Support</div>
    <div class="feature-text">Brightwell Supports provides intensive and ongoing supports that enable clients that may otherwise</div>
  </div>
  <div class="feature" style="left:339px;top:157px">
    <div class="feature-icon"><svg width="40" height="40" viewBox="0 0 40 40"><g fill="none" stroke="#111" stroke-width="4" stroke-dasharray="3 3"><circle cx="14" cy="14" r="8"/><circle cx="30" cy="10" r="5"/><circle cx="15" cy="32" r="5"/></g><circle cx="14" cy="14" r="4" fill="#111"/></svg></div>
    <div class="feature-title">Services</div>
    <div class="feature-text">Brightwell Supports provides intensive and ongoing supports that enable clients that may otherwise</div>
  </div>
  <div class="feature" style="left:553px;top:157px">
    <div class="feature-icon"><svg width="38" height="32" viewBox="0 0 38 32"><path d="M19 2 37 11 19 20 1 11z" fill="#111"/><path d="M1 16l18 9 18-9M1 21l18 9 18-9" fill="none" stroke="#111" stroke-width="3"/></svg></div>
    <div class="feature-title">SLS Program</div>
    <div class="feature-text">Brightwell Supports provides intensive and ongoing supports that enable clients that may otherwise</div>
  </div>
</section>

<h2 class="abs section-title" style="left:127px;top:760px">Welcome To <span>Brightwell Supports</span></h2>
<div class="abs rule" style="left:126px;top:793px;width:285px"></div>
<div class="abs welcome-photo"><div role="img" aria-label="Photo of an office room with a table, red chairs and shelving"></div></div>
<p class="abs welcome-text">Brightwell Supports is an agency designed to creatively serve individuals with developmental disabilities in community-based settings throughout Colorado. Brightwell Supports is an approved service agency through the Division of Developmental Disabilities. Brightwell Supports is an agency designed to creatively serve individuals with developmental disabilities in community-based settings throughout Colorado. Brightwell Supports is an approved service agency through the Division of Developmental Disabilities.</p>
<div class="abs btn">Learn More</div>

<h2 class="abs section-title" style="left:453px;top:760px">Recent <span>Posts</span></h2>
<div class="abs rule" style="left:453px;top:793px;width:301px"></div>

<article class="post" style="top:812px">
  <div class="post-photo"><div role="img" aria-label="Photo of two colleagues working at a computer" style="background:linear-gradient(135deg,#c9d6e6,#8fa8c6 60%,#e8eef5)"></div></div>
  <div class="post-title">Community based residential</div>
  <div class="post-date">March-22-2011</div>
  <div class="post-text">Brightwell Supports provides intensive and ongoing supports that enable clients that may otherwise not be employed in competitive employment.</div>
  <div class="post-more">Read More</div>
</article>
<article class="post" style="top:966px">
  <div class="post-photo"><div role="img" aria-label="Photo of a person working at a desk with a tablet" style="background:linear-gradient(135deg,#e6ebf0,#c7d2dc 60%,#eef1f4)"></div></div>
  <div class="post-title">Community based residential</div>
  <div class="post-date">March-22-2011</div>
  <div class="post-text">Brightwell Supports provides intensive and ongoing supports that enable clients that may otherwise not be employed in competitive employment.</div>
  <div class="post-more">Read More</div>
</article>

<footer class="abs footer">
  <div class="footer-links">Home &nbsp;|&nbsp; Our Company &nbsp;|&nbsp; Available Services &nbsp;|&nbsp; Contact Us</div>
  <div class="footer-copy">©2014 Brightwell Supports, All Rights Reserved.</div>
  <span class="social" style="left:607px"></span>
  <span class="social" style="left:629px"></span>
  <span class="social" style="left:651px"></span>
  <span class="social" style="left:673px"></span>
</footer>

</body>
</html>
```